Web Design For Marlow Pool Service

We are working with a company that wants a website for their pool service. Some sites to use for content/competitors and inspiration:
https://sacramento.brightwaterpoolco.example/builder/newbuild/repair/ppc
https://hollowbrookpoolcareplus.example/
https://lakemontpoolservice.example/
https://www.dravenspoolresurfacing.example/pool-renovation-ga/
Thank you for taking the time to consider designing a website for us. We are web developers based in Stockton, CA, USA. Most of our projects go through the same process. Understanding this process may help you win a project with us. We custom-code all of our websites in-house. We don’t have any requirements as to what tools you use for your design, but we prefer Figma files. For any design that we label as four-stars, we send it to the client for review. The client picks the final design they want us to use. Once we complete this process, we will continue to show additional clients all the four-star sites and purchase them later. Your designs will have multiple chances to sell. For better chances of success, we ask that you follow these guidelines.
IMAGES:
If you use any images or icons in the design, we ask that you have a link to the asset so we can purchase the image/icon. Most of the designs we submit do not have the customer’s images on them unless they have some great images. Be creative; show us the feeling you are trying to portray with your image choices. Use any royalty-free site you choose. We subscribe to Adobe and mainly use their images, but we can purchase images outside of Adobe. PLEASE NOTE: we will not submit designs to clients with watermarks on the images.
FONTS:
We ask that you identify the fonts used in the design. This can be done in a message if you want. We typically use Google Fonts and Adobe Fonts.
CONTENT:
We're always open to different content and ideas. We often submit designs with stock images so the client can see our vision. We typically take pictures after the website launch to use their images with our vision. Lorem Ipsum is fine for paragraphs, but we ask that you write the headers in correct English. We want to be able to show the vision and identify the sections of the website.
INSPIRATION:
We typically add a couple of links in the brief of websites we like to help you get started in your design.
REVISIONS:
We do not often ask for revisions of the designs unless we see something in the design that may not appeal to the client. If there are slight changes that we want to make, we do that in the development process.
FEEDBACK:
We rarely give feedback on designs during the design process. We are working on many website projects and do not have the time to provide feedback. We usually respond if your request is well thought out and asks specific questions, but a note asking “feedback, please” usually goes unanswered.
Number of Pages Required
1 page
Look and feel
Each slider illustrates characteristics of the customer's brand and the style your logo design should communicate.

```html
<!DOCTYPE html>
<html lang="en">
<head>
<meta charset="utf-8">
<title>Marlow Pool Service</title>
<link href="https://fonts.googleapis.com/css2?family=Cinzel:wght@400;500;600&family=Lato:wght@400;700&display=swap" rel="stylesheet">
<style>
:root{
  --royal:#0c4fb6;
  --sky:#2b9be9;
  --accent:#2196f3;
  --ink:#1f1f1f;
  --text:#444;
  --pale:#d7ecfb;
  --teal:#3f6b83;
  --footer:#2b2b2b;
  --white:#fff;
}
*{margin:0;padding:0;box-sizing:border-box}
html,body{width:1200px;height:3843px;overflow:hidden}
body{position:relative;font-family:'Lato',sans-serif;color:var(--text);background:var(--white)}
.abs{position:absolute}
.serif{font-family:'Cinzel',serif}
section,header,footer{position:absolute;left:0;width:1200px}
.photo{position:absolute}

/* hero */
.hero{top:0;height:686px;background:var(--royal);overflow:hidden}
.hero .rule{left:252px;top:0;width:2px;height:686px;background:rgba(120,190,255,.7)}
.brand{left:113px;top:30px;font-family:'Cinzel',serif;font-size:21px;color:var(--white);letter-spacing:2px}
.nav{top:36px;font-size:15px;color:var(--white)}
.phone{left:897px;top:32px;display:flex;align-items:center;gap:14px;color:var(--white);font-weight:700;font-size:16px}
.hero-photo{left:82px;top:298px;width:518px;height:299px;background:linear-gradient(135deg,#3fb0c8,#2a8fb4 55%,#5aa6b0)}
.hero h1{left:113px;top:196px;font-family:'Cinzel',serif;font-weight:500;font-size:57px;line-height:69px;color:var(--white);letter-spacing:1px}
.hero p{left:113px;top:414px;width:300px;font-size:13px;line-height:24px;color:var(--white)}
.card-photo{width:252px;height:412px}
.card-photo span{position:absolute;left:19px;bottom:30px;font-family:'Cinzel',serif;font-size:17px;color:var(--white);letter-spacing:.5px}
.card-photo svg{position:absolute;left:20px;bottom:6px}

/* who */
.who{top:686px;height:535px}
.who h2{left:112px;top:90px;font-family:'Cinzel',serif;font-weight:500;font-size:41px;color:var(--ink)}
.who h3{left:112px;top:155px;width:500px;font-size:22px;line-height:34px;font-weight:400;color:var(--sky)}
.who p{left:112px;top:238px;width:465px;font-size:14.5px;line-height:26px;color:#555}
.who .back{left:685px;top:93px;width:358px;height:325px;background:linear-gradient(135deg,#4d9fe8,#2c7fd4);border-radius:4px}
.who .front{left:651px;top:120px;width:359px;height:321px;background:linear-gradient(180deg,#e8a48c 0%,#6e9fb7 40%,#55905e 62%,#2fa4dc 80%);border-radius:6px;box-shadow:0 12px 30px rgba(0,0,0,.25)}

/* services */
.services{top:1221px;height:643px;background:linear-gradient(160deg,#4d7690,#355f77 50%,#46718b)}
.services h2{width:1200px;top:72px;text-align:center;font-family:'Cinzel',serif;font-weight:500;font-size:42px;color:var(--white)}
.tile{position:absolute;width:326px;height:192px}
.tile.card{background:var(--pale);text-align:center;padding-top:22px}
.tile .num{font-family:'Cinzel',serif;font-size:26px;color:#9bb7cf}
.tile h4{font-family:'Cinzel',serif;font-weight:500;font-size:16px;color:#222;margin-top:8px;letter-spacing:.5px}
.tile p{font-size:12px;line-height:20px;color:#444;width:290px;margin:10px auto 0}
.tile a{display:block;margin-top:4px;font-weight:700;font-size:14px;color:var(--royal);text-decoration:none}
.tile.top{border-top:4px solid var(--sky)}
.tile.top .notch{position:absolute;left:154px;top:-1px;width:0;height:0;border-left:9px solid transparent;border-right:9px solid transparent;border-top:9px solid var(--sky)}

/* testimonials */
.testi{top:1864px;height:491px;text-align:center}
.testi h2{width:1200px;top:88px;font-family:'Cinzel',serif;font-weight:500;font-size:42px;color:var(--ink)}
.testi .quote{left:560px;top:170px}
.testi p{left:170px;top:266px;width:860px;font-size:15px;line-height:24px;color:#444}
.testi .name{width:1200px;top:340px;font-family:'Cinzel',serif;font-size:15px;color:#333}
.dots{left:559px;top:384px;display:flex;gap:8px}
.dots i{width:10px;height:10px;border-radius:50%;border:1.5px solid #666;display:block}
.dots i.on{background:#555}

/* gallery */
.gallery{top:2355px;height:635px;background:#eef2f4}
.gallery .panel{left:69px;top:10px;width:1070px;height:605px;background:linear-gradient(180deg,#d3eaee,#e4f0f2)}
.gallery h2{width:1200px;top:70px;text-align:center;font-family:'Cinzel',serif;font-weight:500;font-size:42px;color:#222}
.btn{display:flex;align-items:center;justify-content:center;border-radius:30px;background:var(--accent);color:var(--white)}
.gallery .btn{left:533px;top:500px;width:134px;height:57px;font-family:'Cinzel',serif;font-size:16px}

/* contact */
.contact{top:2990px;height:538px}
.contact h2{width:1200px;top:80px;text-align:center;font-family:'Cinzel',serif;font-weight:500;font-size:42px;color:var(--ink)}
.info{left:135px;display:flex;align-items:center;gap:24px}
.info .ic{width:50px;height:50px;border-radius:50%;border:1.5px solid var(--sky);display:flex;align-items:center;justify-content:center}
.info b{display:block;font-weight:400;font-size:16px;color:#222}
.info span{font-size:14px;color:#777}
.field{position:absolute;border-bottom:1.5px solid #bbb;font-size:13px;color:#333;padding-bottom:14px}
.contact .btn{left:540px;top:395px;width:152px;height:49px;font-size:15px;font-weight:700}

/* footer */
footer{top:3528px;height:315px;background:var(--footer);color:var(--white)}
footer .brand{width:1200px;left:0;top:66px;text-align:center;color:var(--sky);font-size:28px}
footer .links{top:137px;font-size:15px}
.social{left:495px;top:204px;display:flex;gap:7px}
.social i{display:block;width:36px;height:36px;border:2px solid var(--white);border-radius:50%}
footer .copy{width:1200px;top:253px;text-align:center;font-weight:700;font-size:14.5px}
</style>
</head>
<body>

<header class="hero">
  <div class="abs rule"></div>
  <div class="abs brand">Marlow Pool Service</div>
  <nav>
    <span class="abs nav" style="left:490px">Home</span>
    <span class="abs nav" style="left:571px">About Us</span>
    <span class="abs nav" style="left:674px">Services</span>
    <span class="abs nav" style="left:772px">Contact us</span>
  </nav>
  <div class="abs phone">
    <svg width="26" height="26" viewBox="0 0 24 24" fill="none" stroke="#6fc0ff" stroke-width="1.4"><path d="M22 16.9v3a2 2 0 0 1-2.2 2 19.8 19.8 0 0 1-8.6-3.1 19.5 19.5 0 0 1-6-6A19.8 19.8 0 0 1 2.1 4.2 2 2 0 0 1 4.1 2h3a2 2 0 0 1 2 1.7c.1.9.4 1.8.7 2.7a2 2 0 0 1-.5 2.1L8 9.8a16 16 0 0 0 6 6l1.3-1.3a2 2 0 0 1 2.1-.4c.9.3 1.8.6 2.7.7a2 2 0 0 1 1.7 2z"/></svg>
    +1 (888) 888 8888
  </div>
  <div class="photo hero-photo" role="img" aria-label="Woman in a sun hat relaxing at the edge of a turquoise pool"></div>
  <h1 class="abs">Bring your<br>dream pool to<br>life</h1>
  <p class="abs">Lorem ipsum dolor sit amet, consectetur adipiscing elit, sed do eiusmod tempor incididunt ut labore et dolore magna aliqua. Ut enim minim veniam, quis nostrud sequat.</p>
  <div class="photo card-photo" style="left:616px;top:155px;background:linear-gradient(180deg,#7fb7e6 0%,#5f9a5a 40%,#2f7fbf 70%,#6c5d4e 100%)" role="img" aria-label="Backyard pool with wooden deck and palm">
    <span>Work with the best</span>
    <svg width="16" height="20" viewBox="0 0 16 20" fill="none" stroke="#fff" stroke-width="1.5"><path d="M8 1v17M2 12l6 6 6-6"/></svg>
  </div>
  <div class="photo card-photo" style="left:885px;top:221px;background:linear-gradient(180deg,#4da6e8 0%,#7fc0ee 45%,#9dcdf0 65%,#cfe3f3 100%)" role="img" aria-label="Infinity pool edge with ladder under a blue sky">
    <span>Work with the best</span>
    <svg width="16" height="20" viewBox="0 0 16 20" fill="none" stroke="#fff" stroke-width="1.5"><path d="M8 1v17M2 12l6 6 6-6"/></svg>
  </div>
</header>

<section class="who">
  <h2 class="abs">Who we are</h2>
  <h3 class="abs">Marlow Pool Service includes Pool Cleaning, Pool Repairs and Chemical Pool Service.</h3>
  <p class="abs">Lorem ipsum dolor sit amet, consectetur adipiscing elit, sed do eiusmod tempor incididunt ut labore et dolore magna aliqua. Ut enim ad minim veniam, quis nostrud exercitation ullamco laboris nisi ut aliquip ex ea commodo consequat. Duis aute irure dolor in reprehenderit in voluptate velit esse cillum dolore eu fugiat nulla pariatur. Excepteur sint occaecat cupidatat non proident, sunt in culpa qui officia deserunt mollit anim id est laborum.</p>
  <div class="abs back"></div>
  <div class="photo front" role="img" aria-label="Landscaped pool with rock waterfall at sunset"></div>
</section>

<section class="services">
  <h2 class="abs">What we do</h2>
  <div class="tile photo" style="left:112px;top:164px;background:linear-gradient(180deg,#a9c4d8,#3d8fd1 55%,#2c7cc6)" role="img" aria-label="Worker cleaning an empty tiled pool"></div>
  <div class="tile card" style="left:112px;top:356px">
    <div class="num">01</div><h4>Swimming Pool Services</h4>
    <p>Lorem ipsum dolor sit amet, consectetur adipiscing elit, sed do eiusmod tempor incididunt ut</p><a>Learn More</a>
  </div>
  <div class="tile card top" style="left:438px;top:164px"><span class="notch"></span>
    <div class="num">02</div><h4>Pool Cleaning Services</h4>
    <p>Lorem ipsum dolor sit amet, consectetur adipiscing elit, sed do eiusmod tempor incididunt ut</p><a>Learn More</a>
  </div>
  <div class="tile photo" style="left:438px;top:356px;background:linear-gradient(180deg,#8a9a6e,#c9b27a 35%,#2a9ad8 60%,#1f86c8)" role="img" aria-label="Technician with a robotic pool cleaner at the pool edge"></div>
  <div class="tile photo" style="left:764px;top:164px;background:linear-gradient(135deg,#c4bfb8,#7f98b0 45%,#3f83c8)" role="img" aria-label="Two workers repairing pool mosaic tiles"></div>
  <div class="tile card" style="left:764px;top:356px">
    <div class="num">03</div><h4>Swimming Pool Repair</h4>
    <p>Lorem ipsum dolor sit amet, consectetur adipiscing elit, sed do eiusmod tempor incididunt ut</p><a>Learn More</a>
  </div>
</section>

<section class="testi">
  <h2 class="abs">Testimonials</h2>
  <svg class="abs quote" width="68" height="68" viewBox="0 0 68 68"><circle cx="34" cy="34" r="32" fill="none" stroke="#3aa0ea" stroke-width="1.5"/><text x="34" y="48" text-anchor="middle" font-family="Georgia,serif" font-size="40" font-weight="700" fill="#2b9be9">&#8220;</text></svg>
  <p class="abs">Sed ut perspiciatis unde omnis iste natus error sit voluptatem accusantium doloremque laudantium, totam rem aperiam, eaque ipsa quae ab illo inventore veritatis et quasi architecto beatae vitae dicta sunt explicabo.</p>
  <div class="abs name">Nora Bellamy</div>
  <div class="abs dots"><i></i><i></i><i class="on"></i><i></i><i></i></div>
</section>

<section class="gallery">
  <div class="abs panel"></div>
  <h2 class="abs">Our gallery</h2>
  <div class="photo" style="left:116px;top:152px;width:426px;height:314px;background:linear-gradient(180deg,#b9a98a,#7fa7b8 45%,#5e9ab8)" role="img" aria-label="Family splashing together in a pool"></div>
  <div class="photo" style="left:558px;top:152px;width:258px;height:150px;background:linear-gradient(180deg,#6e8c64,#2f83d0 55%,#2a6fbf)" role="img" aria-label="Backyard pool with stone edging"></div>
  <div class="photo" style="left:825px;top:152px;width:258px;height:150px;background:linear-gradient(135deg,#3cc3d8,#2aa6c6)" role="img" aria-label="Woman floating in clear turquoise water"></div>
  <div class="photo" style="left:558px;top:317px;width:258px;height:149px;background:linear-gradient(135deg,#e0b074,#c98f6e 45%,#3ea6cf)" role="img" aria-label="Mother and daughter hugging in a pool"></div>
  <div class="photo" style="left:825px;top:317px;width:258px;height:149px;background:linear-gradient(180deg,#e8eef2,#b7c2c8 45%,#2c8fd0 75%,#5aa0c8)" role="img" aria-label="Modern white house with rectangular pool"></div>
  <div class="abs btn">View All</div>
</section>

<section class="contact">
  <h2 class="abs">Contact us</h2>
  <div class="abs info" style="top:177px"><div class="ic"><svg width="18" height="18" viewBox="0 0 24 24" fill="none" stroke="#2b9be9" stroke-width="2"><path d="M12 22s7-7 7-12a7 7 0 0 0-14 0c0 5 7 12 7 12z"/><circle cx="12" cy="10" r="2.5"/></svg></div><div><b>ADDRESS</b><span>Lorem Ipsum dummy text 254</span></div></div>
  <div class="abs info" style="top:267px"><div class="ic"><svg width="18" height="18" viewBox="0 0 24 24" fill="none" stroke="#2b9be9" stroke-width="2"><path d="M22 16.9v3a2 2 0 0 1-2.2 2A19.8 19.8 0 0 1 2.1 4.2 2 2 0 0 1 4.1 2h3a2 2 0 0 1 2 1.7l.7 2.7-1.8 3.4a16 16 0 0 0 6 6l3.4-1.8 2.7.7a2 2 0 0 1 1.7 2z"/></svg></div><div><b>PHONE</b><span>+1 888 888 8888</span></div></div>
  <div class="abs info" style="top:351px"><div class="ic"><svg width="18" height="18" viewBox="0 0 24 24" fill="none" stroke="#2b9be9" stroke-width="2"><rect x="7" y="2" width="10" height="20" rx="2"/><path d="M11 18h2"/></svg></div><div><b>EMAIL</b><span>info@marlowpoolservice.com</span></div></div>
  <div class="field" style="left:540px;top:186px;width:251px">First Name :</div>
  <div class="field" style="left:813px;top:186px;width:250px">Last Name :</div>
  <div class="field" style="left:540px;top:255px;width:251px">Email :</div>
  <div class="field" style="left:813px;top:255px;width:250px">Phone :</div>
  <div class="field" style="left:540px;top:334px;width:523px">Message :</div>
  <div class="abs btn">SUBMIT</div>
</section>

<footer>
  <div class="abs brand">Marlow Pool Service</div>
  <span class="abs links" style="left:357px">HOME</span>
  <span class="abs links" style="left:471px">ABOUT US</span>
  <span class="abs links" style="left:613px">SERVICES</span>
  <span class="abs links" style="left:749px">CONTACT US</span>
  <div class="abs social" aria-label="Social links"><i></i><i></i><i></i><i></i><i></i></div>
  <div class="abs copy">©Copyrights 2024 Marlow Pool Service &nbsp;| &nbsp; All Rights Reserved</div>
</footer>

</body>
</html>
```